Theatrical Producer/Consultant needs Artistic Brochure Shell and Inserts

Lanternfield Stageworks (www.lanternfieldstageworks.com) is a small company that offers theatrical producing and consulting services. We would like to create a brochure that contains information about our various productions and services. Because our roster is fluid, we are proposing to create a brochure shell or folder with pockets, and then a template for individual tear sheets that would be inserted into the inside pockets of the brochure shell/folder. The shell is intended for reuse each season, and new tear sheets will be developed separately on a project by project basis.
This task is to create the shell and a corresponding tear sheet template.
The brochure will be delivered by hand as well as by mail, so should fit into a standard size mailing envelope (i.e., within NPDS flat dimensions of 6 1/8" x 11 1/2")
The final design should reflect the high level of artistry of our theatrical projects. Attached are our logo as well as photos of current theatrical offerings which are available for use on the brochure shell but not required. There is also a file that describes our services in more detail, fyi. This will ultimately go onto one of the tear sheets in the brochure.
For the tear sheet template, we have also included a sample brochure from a peer colleague, just to give you an idea of the kind of information each sheet would contain. Each project page will contain title of the project, information about the artists involved, one or more photos, a project description, schedule, fee and other technical information.
The final files for both the shell and tear sheet templates should be printer-ready and also in a file format that we can edit ourselves in future.
Updates
Project Deadline Extended Reason: There was a discrepancy between posted project deadline (December 7) and when project was automatically closed (December 6). Since several designers who have not yet submitted indicated they were planning to submit designs, we wanted to make sure that they were able to do so. Added Monday, December 7, 2015
Industry/Entity Type
Performing Art
Font styles to use
Look and feel
Each slider illustrates characteristics of the customer's brand and the style your logo design should communicate.

```html
<!DOCTYPE html>
<html lang="en">
<head>
<meta charset="utf-8">
<title>Lanternfield Stageworks – Folder Shell</title>
<link href="https://fonts.googleapis.com/css2?family=Lato:ital,wght@0,300;0,400;0,700;1,300&display=swap" rel="stylesheet">
<style>
  :root {
    --ink-blue: #1d8fd6;
    --wash-deep: #3a9ee0;
    --wash-mid: #7cc4f0;
    --wash-pale: #d6ecfa;
    --text-grey: #5f6b75;
    --text-dark: #2d3640;
    --paper: #ffffff;
    --stage-dark: #2a2f3a;
    --stage-warm: #7a5a48;
    --line: #e2e8ee;
  }
  * { box-sizing: border-box; margin: 0; padding: 0; }
  html, body { width: 843px; height: 1200px; overflow: hidden; }
  body {
    position: relative;
    background: var(--paper);
    font-family: "Lato", sans-serif;
    color: var(--text-grey);
  }

  /* ---------- folder shells ---------- */
  .folder {
    position: absolute;
    left: 107px;
    width: 652px;
    display: flex;
    box-shadow: 0 2px 8px rgba(0,0,0,.12);
    background: var(--paper);
  }
  .folder-outside { top: 56px; height: 520px; }
  .folder-inside { top: 640px; height: 535px; }
  .panel { position: relative; width: 326px; height: 100%; overflow: hidden; }
  .panel + .panel { border-left: 1px solid var(--line); }

  .wash {
    background:
      radial-gradient(ellipse 60% 45% at 30% 30%, rgba(255,255,255,.55), transparent 70%),
      radial-gradient(ellipse 70% 60% at 80% 70%, var(--wash-deep), transparent 75%),
      radial-gradient(ellipse 80% 70% at 20% 80%, var(--wash-mid), transparent 80%),
      linear-gradient(160deg, var(--wash-mid), var(--wash-deep));
  }
  .wash-corner {
    position: absolute;
    width: 200px; height: 170px;
    background: radial-gradient(ellipse at center, var(--wash-mid) 0%, rgba(124,196,240,.5) 40%, transparent 70%);
  }

  .pocket-tab {
    position: absolute;
    height: 46px;
    background: linear-gradient(90deg, var(--wash-deep), var(--wash-mid));
    clip-path: polygon(0 0, 100% 0, 88% 100%, 8% 100%);
  }

  /* ---------- wordmark ---------- */
  .wordmark { position: absolute; display: flex; align-items: center; gap: 9px; }
  .wordmark-dot { width: 18px; height: 18px; border-radius: 50%; }
  .wordmark-name { font-weight: 400; font-size: 22px; line-height: 1.05; }
  .wordmark.on-wash .wordmark-dot { background: var(--paper); }
  .wordmark.on-wash .wordmark-name { color: var(--paper); }
  .wordmark.on-paper .wordmark-dot { background: var(--text-dark); }
  .wordmark.on-paper .wordmark-name { color: var(--text-dark); }

  .address {
    position: absolute; left: 52px; top: 458px;
    color: var(--paper); font-size: 10px; line-height: 1.6; font-weight: 300;
  }

  .photo { position: absolute; }
  .photo-stage { background: linear-gradient(180deg, var(--stage-dark) 0%, var(--stage-warm) 65%, #b58a66 100%); }
  .photo-dark { background: linear-gradient(160deg, #1c2027, #4b4f58); }
  .photo-warm { background: linear-gradient(140deg, #6b7a5a, #3d4a38 60%, #a89468); }
  .photo-portrait { background: linear-gradient(150deg, #8a7d70, #4a4038); }

  .headline {
    position: absolute; left: 66px; top: 281px; width: 240px;
    font-weight: 300; font-size: 27px; line-height: 1.12; color: var(--text-grey);
  }
  .headline em { font-style: normal; color: var(--ink-blue); }

  .web {
    position: absolute; font-size: 9px; color: var(--text-grey); letter-spacing: .2px;
  }

  /* ---------- inside pages ---------- */
  .section-title {
    position: absolute; color: var(--ink-blue); font-weight: 400; font-size: 14px; line-height: 1.12;
    white-space: nowrap;
  }
  .body-copy {
    position: absolute; font-size: 7px; line-height: 1.45; color: var(--text-grey);
  }
  .body-copy strong { color: var(--ink-blue); font-weight: 400; font-size: 10px; }
  .body-copy.accent { color: var(--ink-blue); font-style: italic; font-weight: 300; }
</style>
</head>
<body>

<section class="folder folder-outside">
  <div class="panel panel-back wash">
    <div class="wordmark on-wash" style="left:52px; top:318px;">
      <span class="wordmark-dot"></span>
      <span class="wordmark-name">Lanternfield<br>Stageworks</span>
    </div>
    <p class="address">Lanternfield Stageworks<br>214 Alder Row<br>Fairhaven, NJ 08500</p>
  </div>
  <div class="panel panel-cover">
    <div class="wash-corner" style="right:-40px; top:-30px;"></div>
    <div class="wash-corner" style="left:-60px; top:20px; width:180px;"></div>
    <div class="wordmark on-paper" style="left:115px; top:42px;">
      <span class="wordmark-dot"></span>
      <span class="wordmark-name">Lanternfield<br>Stageworks</span>
    </div>
    <div class="photo photo-stage" role="img" aria-label="Stage photograph of an ensemble cast in costume performing" style="left:67px; top:121px; width:225px; height:146px;"></div>
    <h1 class="headline">Dedicated to <em>producing</em> and <em>consulting</em> in the performing arts</h1>
    <p class="web" style="right:22px; top:444px;">www.lanternfieldstageworks.com</p>
  </div>
</section>
<div class="pocket-tab" style="left:126px; top:574px; width:156px;"></div>

<section class="folder folder-inside">
  <div class="panel panel-inner-left">
    <div class="wash-corner" style="left:-60px; top:-40px; width:230px;"></div>
    <div class="wash-corner" style="right:-70px; bottom:-40px;"></div>
    <div class="photo photo-warm" role="img" aria-label="Production photograph of a puppet figure on stage" style="left:10px; top:12px; width:58px; height:116px;"></div>
    <h2 class="section-title" style="left:78px; top:14px;">Lanternfield<br>Stageworks LLC</h2>
    <p class="body-copy" style="left:78px; top:54px; width:100px;">Lanternfield Stageworks is a company dedicated to producing and consulting in the performing arts. We have built lasting partnerships with artists and institutions and bring new work to audiences across the world.</p>
    <div class="photo photo-portrait" role="img" aria-label="Production photograph of a performer in dramatic lighting" style="left:192px; top:12px; width:122px; height:150px;"></div>
    <p class="body-copy" style="left:12px; top:200px; width:150px;"><strong>As producers</strong> we generate and develop our own work and partner with artists and venues to bring bold productions to life on stages everywhere.</p>
    <div class="photo photo-dark" role="img" aria-label="Production photograph of a darkened stage with projected text" style="left:192px; top:186px; width:122px; height:80px;"></div>
    <div class="photo photo-stage" role="img" aria-label="Production photograph of performers under stage lights" style="left:12px; top:292px; width:150px; height:110px;"></div>
    <p class="body-copy" style="left:172px; top:300px; width:140px;"><strong>As consultants</strong> we work with theater companies, presenters and festivals to shape touring strategy, programming, planning and fundraising.</p>
  </div>
  <div class="panel panel-inner-right">
    <div class="wash-corner" style="right:-60px; top:-40px; width:230px;"></div>
    <div class="wash-corner" style="left:-70px; bottom:-30px;"></div>
    <div class="photo photo-portrait" role="img" aria-label="Production photograph of an actor in a close stage moment" style="left:12px; top:12px; width:110px; height:120px;"></div>
    <p class="body-copy" style="left:132px; top:16px; width:180px;">Our model of producing and consulting grows from deep collaboration with artists, presenters and communities, letting each project find its strongest form.</p>
    <p class="body-copy" style="left:12px; top:150px; width:300px;">By collaborating on approach from inception to tour, we help artists and partners reach wider audiences and sustain ambitious creative work.</p>
    <p class="body-copy accent" style="left:12px; top:186px; width:300px;">At its heart, our work is about connecting bold ideas with the people who will care about them most.</p>
    <div class="photo photo-dark" role="img" aria-label="Production photograph of a stage scene with dark set pieces" style="left:12px; top:236px; width:125px; height:80px;"></div>
    <h2 class="section-title" style="left:150px; top:238px;">Lanternfield<br>Stageworks LLC</h2>
    <p class="body-copy" style="left:150px; top:278px; width:160px;">Each season brings new projects and partnerships, and this folder holds details on current work.</p>
    <p class="web" style="left:0; right:0; text-align:center; top:500px;">www.lanternfieldstageworks.com</p>
  </div>
</section>
<div class="pocket-tab" style="left:590px; top:1150px; width:140px; height:40px;"></div>

</body>
</html>
```